Residential Remodeling Contractor needs updated business card

I need a new design for my business card.
Name of the company is Ridgefell Construction. I need a card that commands presence, strength, integrity. I have been in business for 28 years. I am a Residential Remodeling Contractor that covers all aspects of a residential remodel and build.

```html
<!DOCTYPE html>
<html lang="en">
<head>
<meta charset="utf-8">
<title>Ridgefell Construction – Business Card</title>
<link href="https://fonts.googleapis.com/css2?family=Gentium+Book+Plus:wght@400;700&display=swap" rel="stylesheet">
<style>
  :root {
    --page-bg: #d3d4d6;
    --card-dark: #1f3670;
    --card-light: #28468f;
    --ink: #ffffff;
    --ink-soft: #e8ecf6;
  }
  * { margin: 0; padding: 0; box-sizing: border-box; }
  html, body {
    width: 900px;
    height: 1200px;
    overflow: hidden;
    background: var(--page-bg);
    font-family: "Gentium Book Plus", "Palatino Linotype", Georgia, serif;
    color: var(--ink);
  }
  .card {
    position: absolute;
    left: 133px;
    width: 633px;
    height: 364px;
    background: linear-gradient(120deg, var(--card-dark) 0%, var(--card-light) 100%);
  }
  .card--front { top: 210px; }
  .card--back {
    top: 624px;
    background: linear-gradient(200deg, var(--card-light) 0%, var(--card-dark) 60%, var(--card-dark) 100%);
  }
  .wordmark {
    position: absolute;
    font-weight: 700;
    text-transform: uppercase;
    line-height: 1.05;
    color: var(--ink);
    letter-spacing: 0.02em;
  }
  .card--front .wordmark {
    left: 0; right: 0;
    top: 148px;
    text-align: center;
    font-size: 38px;
  }
  .card--back .wordmark {
    right: 48px;
    top: 80px;
    text-align: right;
    font-size: 28px;
  }
  .holder {
    position: absolute;
    left: 40px;
    top: 184px;
  }
  .holder__name {
    font-size: 25px;
    font-weight: 700;
    letter-spacing: 0.04em;
    text-transform: uppercase;
  }
  .holder__role {
    margin-top: 4px;
    font-size: 15px;
    letter-spacing: 0.03em;
    color: var(--ink-soft);
  }
  .contacts {
    position: absolute;
    left: 340px;
    top: 266px;
    list-style: none;
  }
  .contacts__item {
    display: flex;
    align-items: center;
    height: 23.5px;
    font-size: 14px;
    letter-spacing: 0.05em;
    color: var(--ink-soft);
  }
  .contacts__item--phone { letter-spacing: 0.14em; }
  .contacts__icon {
    width: 15px;
    height: 15px;
    margin-right: 7px;
    fill: var(--ink);
    flex: none;
  }
</style>
</head>
<body>
  <section class="card card--front" aria-label="Card front">
    <div class="wordmark">Ridgefell<br>Construction</div>
  </section>

  <section class="card card--back" aria-label="Card back">
    <div class="wordmark">Ridgefell<br>Construction</div>

    <div class="holder">
      <div class="holder__name">Marco Delgado</div>
      <div class="holder__role">Residential Remodeling Contractor</div>
    </div>

    <ul class="contacts">
      <li class="contacts__item contacts__item--phone">
        <svg class="contacts__icon" viewBox="0 0 24 24" aria-hidden="true"><path d="M6.6 10.8a15.1 15.1 0 0 0 6.6 6.6l2.2-2.2c.3-.3.7-.4 1-.2 1.1.4 2.3.6 3.6.6.6 0 1 .4 1 1V20c0 .6-.4 1-1 1A17 17 0 0 1 3 4c0-.6.4-1 1-1h3.5c.6 0 1 .4 1 1 0 1.3.2 2.5.6 3.6.1.3 0 .7-.2 1z"/></svg>
        15550142288
      </li>
      <li class="contacts__item">
        <svg class="contacts__icon" viewBox="0 0 24 24" aria-hidden="true"><path d="M2 5h20v14H2z M3.5 6.5l8.5 6.5 8.5-6.5" fill="none" stroke="#fff" stroke-width="0"/><path d="M2 5h20v2l-10 6.5L2 7z"/><path d="M2 9l10 6.5L22 9v10H2z"/></svg>
        info@ridgefellconstruction.com
      </li>
      <li class="contacts__item">
        <svg class="contacts__icon" viewBox="0 0 24 24" aria-hidden="true"><circle cx="12" cy="12" r="9.5" fill="none" stroke="#fff" stroke-width="1.6"/><ellipse cx="12" cy="12" rx="4" ry="9.5" fill="none" stroke="#fff" stroke-width="1.4"/><path d="M2.5 12h19M4 7h16M4 17h16" stroke="#fff" stroke-width="1.4"/></svg>
        ridgefellconstruction.com
      </li>
    </ul>
  </section>
</body>
</html>
```